Logo and Card design for KRV Home Solutions LLC

I need an edgier logo and business card designs. Current logo attached. I like the colors below. I would like the logo to incorporate a home in the design.
Title = Principal-Acquisitions
Email:KRVHOMESOLUTIONS@fernmail.example
555-214-0937
facebook
IG
2 sided business card with the front being contact info a slogan about selling a home fast. The back incorporating What we do. Buy houses, land, or commercial property as is. We find solutions to make the process of selling simple and fair.

Target Market(s)

Motivated house sellers.

Industry/Entity Type

Business

Contact Information for Business Card

Who we are: We are a Faith based Real Estate Investment Company. We pay cash for homes in any condition and can close quick. Whatever the reason you need to sell fast, we can help. We believe in creating win-win solutions to help you in your time of need. We care! We can help!

Logo Text

KRV Home Solutions LLC

Font styles to use
Sans Serif

Colors
33a6d7
0355a3
85abd2
cee9f5
9d9d9d
b2b2b2
ffffff

Requirements
Must have
• Old logo attached. I want something edgier.
• Company name, phone number, description on the back of what we can do. Pay all cash. Buy in as is condition. No fees,Commisions or closing costs.Close quick. No hassles with solutions to meet your unique situation.
• Call today for an offer within 24 hours.

```html
<!DOCTYPE html>
<html lang="en">
<head>
<meta charset="utf-8">
<title>KRV Home Solutions – Business Card</title>
<link rel="stylesheet" href="https://fonts.googleapis.com/css2?family=Work+Sans:wght@400;500;600;700&display=swap">
<style>
  :root {
    --navy: #1f3468;
    --ink: #4a4a4a;
    --grey: #9d9d9d;
    --sky: #33a6d7;
    --paper: #ffffff;
    --backdrop: #e9e9e9;
  }
  * { box-sizing: border-box; margin: 0; padding: 0; }
  html, body {
    width: 1200px; height: 1004px; overflow: hidden;
    background: var(--backdrop);
    font-family: "Work Sans", Arial, sans-serif;
  }
  .card {
    position: absolute; left: 298px; width: 600px; height: 343px;
    overflow: hidden;
    box-shadow: 0 2px 6px rgba(0,0,0,.25);
  }
  .card--front { top: 130px; background: var(--paper); border-right: 2px solid var(--sky); }
  .card--back { top: 527px; background: var(--navy); }

  .brand { position: absolute; display: flex; align-items: center; gap: 9px;
    font-weight: 700; letter-spacing: .4px; white-space: nowrap; }
  .brand__mark { width: 12px; height: 12px; flex: none; }
  .card--front .brand { left: 56px; top: 157px; width: 222px; color: var(--navy); font-size: 15.5px; }
  .card--front .brand__mark { background: var(--navy); }
  .card--back .brand { left: 0; right: 0; top: 124px; justify-content: center; color: var(--paper); font-size: 24px; }
  .card--back .brand__mark { background: var(--paper); width: 18px; height: 18px; }

  .divider { position: absolute; left: 290px; top: 84px; width: 2px; height: 141px; background: var(--navy); }

  .identity { position: absolute; left: 306px; top: 86px; white-space: nowrap; }
  .identity__name { font-size: 23px; font-weight: 700; color: var(--navy); letter-spacing: .3px; }
  .identity__title { font-size: 14px; color: var(--ink); margin-top: 2px; }

  .contacts { position: absolute; left: 310px; top: 156px; list-style: none; }
  .contacts li { display: flex; align-items: center; gap: 9px; height: 18px;
    font-size: 13.5px; color: var(--ink); white-space: nowrap; }
  .contacts svg { width: 11px; height: 11px; flex: none; }

  .slogan-band { position: absolute; left: 0; right: 0; bottom: 3px; height: 27px; background: var(--navy);
    display: flex; align-items: center; justify-content: center;
    color: var(--paper); font-size: 14px; font-weight: 600; letter-spacing: .6px; }
  .slogan-band__rule { position: absolute; top: 0; width: 2px; height: 100%; background: var(--paper); }

  .offer { position: absolute; left: 0; right: 0; top: 240px; text-align: center;
    color: var(--paper); font-size: 15.5px; line-height: 19px; }
</style>
</head>
<body>
  <section class="card card--front">
    <div class="brand"><span class="brand__mark"></span>KRV HOME SOLUTIONS</div>
    <div class="divider"></div>
    <div class="identity">
      <h1 class="identity__name">KRV HOME SOLUTIONS</h1>
      <p class="identity__title">Principal-Acquisitions</p>
    </div>
    <ul class="contacts">
      <li><svg viewBox="0 0 12 12"><circle cx="6" cy="6" r="6" fill="#1f3468"/><path d="M4 3.2l1.1 1.3-.6.7c.4.9 1.1 1.6 2 2l.7-.6 1.3 1.1-.7 1c-2.2-.3-4-2.1-4.3-4.3z" fill="#fff"/></svg>555-214-0937</li>
      <li><svg viewBox="0 0 12 12"><circle cx="6" cy="6" r="6" fill="#1f3468"/></svg>/krvhomesolutions</li>
      <li><svg viewBox="0 0 12 12"><circle cx="6" cy="6" r="6" fill="#1f3468"/></svg>@krvhomesolutions</li>
      <li><svg viewBox="0 0 12 12"><circle cx="6" cy="6" r="6" fill="#1f3468"/><rect x="3" y="4" width="6" height="4.2" fill="none" stroke="#fff" stroke-width=".9"/><path d="M3 4l3 2.3L9 4" fill="none" stroke="#fff" stroke-width=".9"/></svg>krvhomesolutions@fernmail.example</li>
    </ul>
    <div class="slogan-band">
      <span class="slogan-band__rule" style="left:57px"></span>
      SELLING A HOME FAST
      <span class="slogan-band__rule" style="left:541px"></span>
    </div>
  </section>

  <section class="card card--back">
    <div class="brand"><span class="brand__mark"></span>KRV HOME SOLUTIONS</div>
    <p class="offer">
      Pay all cash. Buy in as is condition. No fees,Commisions<br>
      or closing costs.Close quick. No hassles with solutions<br>
      to meet your unique situation.<br>
      Call today for an offer within 24 hours.
    </p>
  </section>
</body>
</html>
```